Tidewater Motion Bodywork needs a Website

I'm a Massage Practitioner wanting a website for promotion and bookings with a Blog area and inplementation to my facebook page https://www.pagewall-social.com/TidewaterMotionBodywork , my setmore Booking page http://my.slotkeeper.net/bookingpage/a73e2d41-5b6c-4e82-9f07-c18d25e6b3a0 and my PayPal account to make payments.
The Venues changes from time to time. In October 2015 it will be the Coralspan Endurance Worldchampionship in Kona Hawaii

Target Market(s)

Sports People participating in targeted Events

Industry/Entity Type

Massage

Number of Pages Required

5+ page

Font styles to use
Other font styles liked:
• Verdana

Colors
3176b5
5db8de
ec1f27
ffffff

Requirements
Must have
• An About page including which events (in this case Coralspan Endurance World Championship in Kona, Hawaii in October 2015)
• A page with the Techniques I use
• Inplementation of my Setmore Booking Page http://my.slotkeeper.net/bookingpage/a73e2d41-5b6c-4e82-9f07-c18d25e6b3a0
• Implementation of my Facebook Page https://www.pagewall-social.com/TidewaterMotionBodywork
Nice to have
• Would be great to have a Blog with Pictures Upload ability
• Tried to upload Pictures but it always says that it is a non supported file type, so contact me to send you those informations. More informations about me to be found on http://wellroot.com.au/about-us/meet-the-team/jon-harlow-pike---massage-therapist.html

```html
<!DOCTYPE html>
<html lang="en">
<head>
<meta charset="utf-8">
<title>Tidewater Motion Bodywork</title>
<link href="https://fonts.googleapis.com/css2?family=Open+Sans:ital,wght@0,400;0,600;1,400&display=swap" rel="stylesheet">
<style>
:root{
  --red:#e0141e;
  --blue:#3176b5;
  --sky:#5db8de;
  --text:#8a8a8a;
  --dark:#3a3a3a;
  --band:#f1f1f1;
  --footer:#3b3b3b;
  --white:#ffffff;
}
*{margin:0;padding:0;box-sizing:border-box}
html,body{width:751px;height:1200px;overflow:hidden;background:var(--white);font-family:"Open Sans",Verdana,sans-serif}
.page{position:relative;width:751px;height:1200px}
.header{position:absolute;top:0;left:0;width:751px;height:78px}
.brand{position:absolute;left:62px;top:22px;display:flex;align-items:center;gap:7px}
.brand-dot{width:26px;height:26px;border-radius:50%;background:var(--sky)}
.brand-name{color:var(--red);font-size:12px;line-height:14px;width:90px;font-weight:400}
.call{position:absolute;right:63px;top:19px;display:flex;align-items:center;gap:4px}
.call-text{text-align:right;line-height:11px}
.call-text small{display:block;font-size:7px;color:var(--text)}
.call-text span{font-size:11px;color:var(--blue)}
.call-icon{width:21px;height:19px;background:var(--blue);display:flex;align-items:center;justify-content:center}
.nav{position:absolute;right:63px;top:56px;display:flex;gap:27px;font-size:7.5px;color:#777}
.nav .active{color:var(--red)}
.hero{position:absolute;top:78px;left:0;width:751px;height:333px;background:linear-gradient(120deg,#5a5550 0%,#8b8680 35%,#c7c2bb 60%,#6c6c70 100%)}
.hero .arrow{position:absolute;top:155px;width:16px;height:22px;background:rgba(0,0,0,.25)}
.welcome{position:absolute;top:443px;left:0;width:751px;text-align:center}
.welcome h1{font-size:17.5px;font-weight:400;color:var(--red)}
.welcome p{width:545px;margin:10px auto 0;font-size:7.3px;line-height:14px;color:var(--text)}
.divider{position:absolute;top:549px;left:62px;width:626px;height:1px;background:#ddd}
.services-title{position:absolute;top:572px;width:751px;text-align:center;font-size:17.5px;font-weight:400;color:var(--red)}
.service{position:absolute;top:609px;width:201px}
.service .photo{height:116px}
.service h3{margin-top:8px;font-size:8.5px;font-weight:400;color:var(--blue)}
.service p{margin-top:4px;font-size:6.4px;line-height:12px;color:#aaa}
.band{position:absolute;top:822px;left:0;width:751px;height:260px;background:var(--band)}
.panel{position:absolute;background:var(--white);top:842px;height:221px}
.panel h2{position:absolute;left:11px;top:14px;font-size:13px;font-weight:400;color:var(--dark)}
.testimonials{left:63px;width:451px}
.portrait{position:absolute;left:11px;top:40px;width:136px;height:140px;background:linear-gradient(140deg,#c9d7e6,#e2c7b0 55%,#7c9bc4)}
.quote-name{position:absolute;left:166px;top:47px;font-size:11px;color:var(--dark)}
.quote-name small{font-size:7px}
.quote{position:absolute;left:165px;top:72px;width:265px;font-size:7px;line-height:16px;font-style:italic;color:#666}
.quote .mark{font-size:22px;font-style:normal;font-weight:600;color:#555;line-height:0;vertical-align:-7px;margin:0 3px}
.dots{position:absolute;left:11px;top:196px;display:flex;gap:3px}
.dots i{width:8px;height:8px;border-radius:50%;border:1px solid #bbb}
.dots i.on{background:#999;border-color:#999}
.booking{left:525px;width:163px}
.field{position:absolute;left:11px;width:137px;height:17px;border:1px solid #ddd;font-size:6.5px;color:#888;padding:4px 8px}
.field.tall{height:44px}
.submit{position:absolute;left:11px;top:194px;width:39px;height:17px;background:var(--dark);color:var(--white);font-size:7.5px;font-weight:600;display:flex;align-items:center;justify-content:center;border-radius:2px}
.contact{position:absolute;top:1082px;width:751px;height:49px;display:flex;align-items:center;justify-content:center;gap:12px;font-size:7.5px;color:#555}
.contact span{display:flex;align-items:center;gap:4px}
.contact .sep{color:#999}
.footer{position:absolute;top:1131px;left:0;width:751px;height:69px;background:var(--footer)}
.footer-nav{position:absolute;left:63px;top:22px;font-size:6.5px;color:#ddd;word-spacing:2px}
.copyright{position:absolute;left:63px;top:39px;font-size:6.5px;color:#ddd}
.social{position:absolute;right:63px;top:25px;display:flex;gap:8px}
.social i{width:16px;height:16px;border-radius:50%}
</style>
</head>
<body>
<div class="page">
  <header class="header">
    <div class="brand"><div class="brand-dot"></div><div class="brand-name">Tidewater Motion Bodywork</div></div>
    <div class="call">
      <div class="call-text"><small>Call us</small><span>+61455210387</span></div>
      <div class="call-icon"><svg width="9" height="9" viewBox="0 0 24 24"><path fill="#fff" d="M6.6 10.8a15 15 0 006.6 6.6l2.2-2.2c.3-.3.7-.4 1-.2 1.1.4 2.3.6 3.6.6.6 0 1 .4 1 1V20c0 .6-.4 1-1 1A17 17 0 013 4c0-.6.4-1 1-1h3.5c.6 0 1 .4 1 1 0 1.3.2 2.5.6 3.6.1.3 0 .7-.2 1z"/></svg></div>
    </div>
    <nav class="nav"><span class="active">Home</span><span>About us</span><span>Services</span><span>Products</span><span>Testimonials</span><span>Contact us</span></nav>
  </header>

  <section class="hero" role="img" aria-label="Therapist massaging an athlete's leg in a treatment room">
    <div class="arrow" style="left:0"></div><div class="arrow" style="right:0"></div>
  </section>

  <section class="welcome">
    <h1>Welcome to Tidewater Motion Bodywork</h1>
    <p>Wellroot360 is a one stop destination for all your sports, work, and active lifestyle injuries. We specialise in providing multi-disciplinary practitioner choices all under one roof. We all work together to ensure your return to optimal health and performance. Wellroot360 is unique in that we provide one on one customised examinations, treatment, and functional rehabilitation. We use state-of-the-art equipment, protocols, and treatments to optimise your patient's recovery and prevent reoccurrences.</p>
  </section>
  <div class="divider"></div>

  <h2 class="services-title">Our Services</h2>
  <article class="service" style="left:62px">
    <div class="photo" role="img" aria-label="Deep tissue massage on a sports table" style="background:linear-gradient(135deg,#b9b5ad,#e6e3dc 50%,#6b5f55)"></div>
    <h3>Sport Deep Tissue Massage</h3>
    <p>Donec diam mi, laoreet eu enim vitae, volutpat placerat eros. Duis volutpat, ante dictum porttitor sodales, metus felis aliquet est, quis vehicula ligula dolor vel mi.</p>
  </article>
  <article class="service" style="left:275px">
    <div class="photo" role="img" aria-label="Myofascial release treatment in a clinic" style="background:linear-gradient(135deg,#6f8a6a,#c9b9a6 50%,#8a6f92)"></div>
    <h3>Myofascial Release</h3>
    <p>Donec diam mi, laoreet eu enim vitae, volutpat placerat eros. Duis volutpat, ante dictum porttitor sodales, metus felis aliquet est, quis vehicula ligula dolor vel mi.</p>
  </article>
  <article class="service" style="left:487px">
    <div class="photo" role="img" aria-label="Active soft tissue work on a seated athlete" style="background:linear-gradient(135deg,#7d7566,#d8d0bd 50%,#5a4636)"></div>
    <h3>Sport Deep Tissue with Active Soft Tissue Work</h3>
    <p>Donec diam mi, laoreet eu enim vitae, volutpat placerat eros. Duis volutpat, ante dictum porttitor sodales, metus felis aliquet est, quis vehicula ligula dolor vel mi.</p>
  </article>

  <div class="band"></div>
  <section class="panel testimonials">
    <h2>TESTIMONIALS</h2>
    <div class="portrait" role="img" aria-label="Portrait of a satisfied client"></div>
    <div class="quote-name">Mark Dalton, <small>City</small></div>
    <p class="quote"><span class="mark">&ldquo;</span>Donec vestibulum odio sem, ac laoreet massa ullam corper id. Donec nisi et tellus hendrerit vehicula. Nunc eu ligula sed quam pulvinar maximus in vitae eros. Proin porta fermentum , vel porttitor turpis venenatis luctus. Vivamus volutpat sapien quis tempus. Donec diam mi, laoreet eu enim vitae, volutpat placerat eros. Duis volutpat, ante dictum porttitor sodales, metus felis aliquet est, quis vehicula ligula dolor vel mi.<span class="mark">&rdquo;</span></p>
    <div class="dots"><i class="on"></i><i></i><i></i><i></i><i></i><i></i><i></i></div>
  </section>
  <section class="panel booking">
    <h2>BOOK APPOINTMENT</h2>
    <div class="field" style="top:40px">Name</div>
    <div class="field" style="top:66px">E-mail</div>
    <div class="field" style="top:92px">Phone</div>
    <div class="field" style="top:116px">Date
      <svg style="position:absolute;right:6px;top:4px" width="8" height="8" viewBox="0 0 8 8"><rect x=".5" y="1.5" width="7" height="6" fill="none" stroke="#bbb"/><line x1=".5" y1="3.5" x2="7.5" y2="3.5" stroke="#bbb"/></svg>
    </div>
    <div class="field tall" style="top:142px">Details</div>
    <div class="submit">SUBMIT</div>
  </section>

  <section class="contact">
    <span><svg width="8" height="8" viewBox="0 0 24 24"><path fill="#666" d="M6.6 10.8a15 15 0 006.6 6.6l2.2-2.2c.3-.3.7-.4 1-.2 1.1.4 2.3.6 3.6.6.6 0 1 .4 1 1V20c0 .6-.4 1-1 1A17 17 0 013 4c0-.6.4-1 1-1h3.5c.6 0 1 .4 1 1 0 1.3.2 2.5.6 3.6.1.3 0 .7-.2 1z"/></svg>Contact us today! +61455210387</span>
    <span class="sep">|</span>
    <span><svg width="7" height="9" viewBox="0 0 14 20"><path fill="#666" d="M7 0a7 7 0 00-7 7c0 5 7 13 7 13s7-8 7-13a7 7 0 00-7-7zm0 9.5A2.5 2.5 0 117 4.5a2.5 2.5 0 010 5z"/></svg>Pelican Shore House 12-4410 Coral Drive, Kailua-Kona, HI 96740</span>
    <span class="sep">|</span>
    <span><svg width="9" height="7" viewBox="0 0 18 14"><rect width="18" height="14" fill="#666"/><path d="M1 1l8 6 8-6" fill="none" stroke="#fff" stroke-width="1.5"/></svg>info@tidewatermotionbodywork.com</span>
  </section>

  <footer class="footer">
    <div class="footer-nav">Home &nbsp;|&nbsp; About us &nbsp;|&nbsp; Services &nbsp;|&nbsp; Products &nbsp;|&nbsp; Testimonials &nbsp;|&nbsp; Contact us</div>
    <div class="copyright">Copyright &copy; 2015 &nbsp;Tidewater Motion Bodywork. &nbsp;All rights reserved.</div>
    <div class="social"><i style="background:#3b5998"></i><i style="background:var(--sky)"></i><i style="background:var(--blue)"></i></div>
  </footer>
</div>
</body>
</html>
```